QVR business card

Need a business card for a company that provides instructional design and elearning development services. The website is here: http://quorvane.studio/

I'm attaching a current logo, as well as the old business card design. While I like to keep it clean, the old design is too simplistic for my liking. The only idea I want to reuse from the old design is placing industry jargon on the back of the card, just need a better way to present it. But if you have other ideas for the back--feel free to experiment.

Please use the colors complementary to the color we have on the website. Thank you!

```html
<!DOCTYPE html>
<html lang="en">
<head>
<meta charset="utf-8">
<title>QVR Business Card</title>
<link rel="stylesheet" href="https://fonts.googleapis.com/css2?family=Open+Sans:wght@400;600;700&family=Montserrat:wght@700;800&display=swap">
<style>
  :root {
    --teal: #1fb8b2;
    --teal-deep: #12a6a3;
    --teal-light: #5fd0cc;
    --sand: #e6d69a;
    --gold: #c9b46a;
    --white: #ffffff;
    --ink: #1e2b2b;
    --stage: #e9ebeb;
  }
  * { box-sizing: border-box; margin: 0; padding: 0; }
  html, body { width: 1200px; height: 726px; overflow: hidden; }
  body {
    background: var(--stage);
    font-family: "Open Sans", Arial, sans-serif;
    position: relative;
  }
  .card {
    position: absolute;
    width: 540px;
    height: 309px;
    overflow: hidden;
    box-shadow: 0 6px 18px rgba(0,0,0,.14);
  }
  /* Front */
  .card-front { left: 40px; top: 208px; background: var(--white); }
  .brand-panel {
    position: absolute; left: 0; top: 0; width: 238px; height: 100%;
    display: flex; align-items: center; justify-content: center; gap: 10px;
  }
  .brand-dot { width: 26px; height: 26px; border-radius: 50%; background: var(--teal); }
  .brand-name {
    font-family: "Open Sans", Arial, sans-serif; font-weight: 700;
    font-size: 40px; color: var(--gold); letter-spacing: 1px;
  }
  .icon-band {
    position: absolute; left: 238px; top: 0; width: 44px; height: 100%;
    background: var(--teal);
    border-left: 3px solid var(--gold); border-right: 3px solid var(--gold);
  }
  .icon-band .stripe {
    position: absolute; left: 0; width: 100%; height: 18px; background: var(--teal-light);
  }
  .icon-pill {
    position: absolute; left: 7px; top: 112px; width: 24px; height: 86px;
    border-radius: 12px; background: var(--sand);
    display: flex; flex-direction: column; align-items: center; justify-content: space-evenly;
  }
  .details-panel {
    position: absolute; left: 282px; top: 0; right: 0; height: 100%;
    background: linear-gradient(225deg, var(--teal) 0%, #6cc3b0 45%, var(--sand) 100%);
    padding: 96px 0 0 22px; color: var(--white);
  }
  .person-name {
    font-family: "Montserrat", Arial, sans-serif; font-weight: 800;
    font-size: 17px; letter-spacing: 1px; text-transform: uppercase;
  }
  .person-role { color: var(--ink); font-size: 13px; margin-bottom: 10px; }
  .contact-line { font-size: 13px; line-height: 19px; }
  /* Back */
  .card-back {
    left: 620px; top: 208px;
    background: linear-gradient(180deg, var(--teal) 0%, #8fc7ad 55%, var(--sand) 100%);
    color: var(--white); text-align: center;
  }
  .map-area {
    position: absolute; left: 120px; top: 100px; width: 400px; height: 160px;
    background: radial-gradient(ellipse at center, rgba(18,140,140,.28), rgba(18,140,140,0) 70%);
  }
  .back-mark {
    position: absolute; left: 0; right: 0; top: 62px;
    display: flex; justify-content: center; align-items: center; gap: 10px;
  }
  .back-mark .brand-dot { background: var(--white); width: 22px; height: 22px; }
  .back-mark .brand-name { color: var(--white); font-size: 38px; }
  .service-list {
    position: absolute; left: 0; right: 0; top: 140px;
    display: flex; flex-direction: column; align-items: center; gap: 3px;
  }
  .service-tag {
    background: var(--teal-deep); padding: 0 6px;
    font-size: 15px; line-height: 21px; border-radius: 2px;
  }
  .back-url { position: absolute; left: 0; right: 0; top: 244px; font-size: 12px; }
</style>
</head>
<body>
  <section class="card card-front">
    <div class="brand-panel">
      <span class="brand-dot"></span>
      <span class="brand-name">QVR</span>
    </div>
    <div class="icon-band">
      <span class="stripe" style="top:22px"></span>
      <span class="stripe" style="top:62px"></span>
      <span class="stripe" style="top:229px"></span>
      <span class="stripe" style="top:269px"></span>
      <div class="icon-pill">
        <svg width="14" height="14" viewBox="0 0 14 14" aria-label="Phone"><path d="M3 1 L5.5 1 L6.5 4 L5 5.2 Q6.5 8 8.8 9 L10 7.5 L13 8.5 L13 11 Q12 13 10 13 Q2 11 1 3 Q1 1 3 1Z" fill="#12a6a3"/></svg>
        <svg width="14" height="12" viewBox="0 0 14 12" aria-label="Email"><rect x="1" y="2" width="12" height="8" fill="none" stroke="#12a6a3" stroke-width="1.5"/><path d="M1 2 L7 7 L13 2" fill="none" stroke="#12a6a3" stroke-width="1.5"/></svg>
        <svg width="14" height="14" viewBox="0 0 14 14" aria-label="Website"><circle cx="7" cy="7" r="6" fill="none" stroke="#12a6a3" stroke-width="1.5"/><path d="M1 7 H13 M7 1 Q3 7 7 13 M7 1 Q11 7 7 13" fill="none" stroke="#12a6a3" stroke-width="1.2"/></svg>
      </div>
    </div>
    <div class="details-panel">
      <p class="person-name">Adrian Velmont</p>
      <p class="person-role">Managing Director</p>
      <p class="contact-line">555-010-4827</p>
      <p class="contact-line">avelmont@quorvane.studio</p>
      <p class="contact-line">www.quorvane.studio</p>
    </div>
  </section>

  <section class="card card-back">
    <div class="map-area" role="img" aria-label="Dotted world map"></div>
    <div class="back-mark">
      <span class="brand-dot"></span>
      <span class="brand-name">QVR</span>
    </div>
    <div class="service-list">
      <span class="service-tag">Instructional Design</span>
      <span class="service-tag">Elearning Development | Mobile Learning</span>
      <span class="service-tag">Instructor-LED Training</span>
    </div>
    <p class="back-url">www.quorvane.studio</p>
  </section>
</body>
</html>
```